Dynamic Business Card for Sports Supplements Company

Hi! I'm looking for an awesome business card to match my existing sports supplement company. I have uploaded my current company logo and screenshot of the front page of my website.

I would like to have something dynamic and interesting and utilize the colors in the website - the reds and purples

The business card should be double sided and focus on a unique eye-catching design on the back and include all the relevant company info.

Most importantly, it should say somewhere: "Sign up on our website for a coupon code."

Target Market(s)

Mostly for women gym goers but it shouldn't be too feminine. It should be in keeping with the website design. It should flow and clearly be connected to it

Industry/Entity Type

Business

Contact Information for Business Card

Lorraine K. Vestal
CEO
LVestal@Quorvanexco.com
www.quorvanexco.com
555.417.3820
P.O. Box 47315
Fenmoor, Calderra 00000

Sign up on our website for a coupon code

Font styles to use
Serif
Sans Serif
Other font styles liked:
• Novecento font family and "Quorvanex" is in AR Destine font

Requirements
Must have
• One side should be a bold Quorvanex logo design. Even just the symbol itself may be o.k. (see attached file)

```html
<!DOCTYPE html>
<html lang="en">
<head>
<meta charset="utf-8">
<title>Quorvanex Business Card</title>
<link href="https://fonts.googleapis.com/css2?family=Open+Sans:wght@400;600;700;800&display=swap" rel="stylesheet">
<style>
  :root{
    --stage:#e9e6e1;
    --ink:#1f1f1f;
    --card-black:#1c1c1c;
    --red:#e0262f;
    --white:#ffffff;
    --grey-light:#f2f2f2;
    --grey-mid:#cfcfcf;
    --text-light:#f1f1f1;
  }
  *{margin:0;padding:0;box-sizing:border-box}
  html,body{width:1200px;height:780px;overflow:hidden}
  body{background:var(--stage);font-family:"Open Sans",Arial,sans-serif;position:relative}

  .card{position:absolute;width:540px;height:310px;border-radius:3px;overflow:hidden;
        box-shadow:0 10px 24px rgba(0,0,0,.18),0 2px 4px rgba(0,0,0,.12)}
  .card--front{left:50px;top:80px;background:var(--white)}
  .card--back{left:610px;top:390px;background:radial-gradient(ellipse at 60% 40%,var(--grey-light) 0%,#e4e4e4 55%,var(--grey-mid) 100%)}

  .front-shape{position:absolute;inset:0;width:100%;height:100%}

  .brand{position:absolute;display:flex;align-items:center;gap:10px}
  .brand__mark{width:22px;height:22px;background:var(--red);flex:none}
  .brand__name{font-weight:800;color:var(--ink);letter-spacing:2px;text-transform:uppercase;white-space:nowrap}
  .card--front .brand{left:34px;top:194px}
  .card--front .brand__name{font-size:26px}

  .contact{position:absolute;left:330px;top:34px;color:var(--text-light)}
  .contact__name{color:var(--red);font-weight:700;font-size:19px;line-height:1.2}
  .contact__role{font-size:13px;margin-top:2px}
  .contact__address{font-size:12.5px;line-height:1.5;margin-top:32px}
  .contact__lines{list-style:none;margin-top:12px;font-size:12.5px;line-height:1.55}
  .contact__lines li{display:flex;align-items:center;gap:7px}
  .contact__icon{width:14px;height:14px;flex:none}
  .accent{color:var(--red)}

  .card--back .brand{left:250px;top:118px}
  .card--back .brand__name{font-size:30px}
  .coupon{position:absolute;left:40px;top:250px;font-size:14px;color:var(--ink)}
  .coupon .accent{font-weight:600}
</style>
</head>
<body>

<section class="card card--front" aria-label="Card front">
  <svg class="front-shape" viewBox="0 0 540 310" preserveAspectRatio="none" aria-hidden="true">
    <path d="M272,0 C222,90 322,200 240,310 L540,310 L540,0 Z" fill="var(--red)"/>
    <path d="M290,0 C240,90 340,200 258,310 L540,310 L540,0 Z" fill="var(--card-black)"/>
  </svg>

  <div class="brand">
    <span class="brand__mark"></span>
    <span class="brand__name">Quorvanex</span>
  </div>

  <div class="contact">
    <p class="contact__name">Lorraine K. Vestal</p>
    <p class="contact__role">CEO</p>
    <p class="contact__address">P.O. Box 47315<br>Fenmoor, Calderra 00000</p>
    <ul class="contact__lines">
      <li>
        <svg class="contact__icon" viewBox="0 0 14 14"><rect width="14" height="14" fill="var(--red)"/><path d="M4 3.5h2l.8 2-1.2.9a5 5 0 0 0 2 2l.9-1.2 2 .8v2c0 .5-.4.8-.9.8A6.5 6.5 0 0 1 3.2 4.4c0-.5.3-.9.8-.9z" fill="#fff"/></svg>
        <span>555.417.3820</span>
      </li>
      <li>
        <svg class="contact__icon" viewBox="0 0 14 14"><rect width="14" height="14" fill="var(--red)"/><rect x="3" y="4" width="8" height="6" fill="none" stroke="#fff" stroke-width="1"/><path d="M3 4l4 3.2L11 4" fill="none" stroke="#fff" stroke-width="1"/></svg>
        <span>LVestal@Quorvanexco.com</span>
      </li>
      <li>
        <svg class="contact__icon" viewBox="0 0 14 14"><rect width="14" height="14" fill="var(--red)"/><circle cx="7" cy="7" r="4" fill="none" stroke="#fff" stroke-width="1"/><path d="M3 7h8M7 3c-2 2.4-2 5.6 0 8M7 3c2 2.4 2 5.6 0 8" fill="none" stroke="#fff" stroke-width=".8"/></svg>
        <span>www.<span class="accent">quorvanexco</span>.com</span>
      </li>
    </ul>
  </div>
</section>

<section class="card card--back" aria-label="Card back">
  <div class="brand">
    <span class="brand__mark"></span>
    <span class="brand__name">Quorvanex</span>
  </div>
  <p class="coupon"><span class="accent">Sign up</span> on our website for a coupon code</p>
</section>

</body>
</html>
```